Verlindo Magician

I want the business card for my business to give to people who watch that later I will be employed to show magic here is my website http://www.balsamomagicien.com/I want the interesting design , i am very opened for formal and informal, I watch a lot of design so don't stick to the common shape and form but i hope it can also be produced the thing to write on will be the same as in picture that i will upload , i also will upload the logo for you that so can be easy to useDenis CostilleMagicianMAGICIAN BALSAMO 17 rue des Tilleuls - 48120 VALMOREY contact@verlindoillusions.example tel. 0547 946 157 tel. 0674 219 503

```html
<!DOCTYPE html>
<html lang="fr">
<head>
<meta charset="utf-8">
<title>Verlindo Magician – Business Card</title>
<link href="https://fonts.googleapis.com/css2?family=Jost:wght@400&display=swap" rel="stylesheet">
<style>
  :root {
    --backdrop: #1c1b1b;
    --ink: #000000;
    --paper: #ffffff;
    --accent: #e31e24;
    --muted: #555555;
    --ghost: #e6e6e6;
  }
  html, body {
    margin: 0;
    padding: 0;
    width: 1125px;
    height: 1200px;
    overflow: hidden;
    background: var(--backdrop);
    font-family: "Jost", "Futura", sans-serif;
  }
  .canvas {
    position: relative;
    width: 1125px;
    height: 1200px;
  }
  .card {
    position: absolute;
    left: 171px;
    width: 826px;
    height: 471px;
    background: var(--paper);
    overflow: hidden;
  }
  .card--front { top: 106px; }
  .card--back  { top: 639px; }

  /* Front card */
  .contact-panel {
    position: absolute;
    left: 0; top: 0;
    width: 392px;
    height: 100%;
    background: var(--ink);
    color: var(--paper);
  }
  .person-name {
    position: absolute;
    left: 44px; top: 80px;
    margin: 0;
    font-size: 31px;
    font-weight: 400;
    line-height: 1.1;
    color: var(--accent);
  }
  .person-role {
    position: absolute;
    left: 44px; top: 116px;
    margin: 0;
    font-size: 21px;
    line-height: 1.2;
  }
  .address {
    position: absolute;
    left: 44px; top: 184px;
    margin: 0;
    font-style: normal;
    font-size: 20px;
    line-height: 25px;
  }
  .contact-list {
    position: absolute;
    left: 44px; top: 275px;
    margin: 0; padding: 0;
    list-style: none;
    font-size: 20px;
    line-height: 26.5px;
  }
  .contact-list li {
    display: flex;
    align-items: center;
  }
  .contact-list .small { font-size: 18.5px; }
  .contact-icon {
    width: 18px; height: 18px;
    margin-right: 12px;
    flex: none;
    fill: var(--accent);
  }
  .brand-panel {
    position: absolute;
    left: 392px; top: 0;
    width: 434px;
    height: 100%;
  }
  .portrait-front {
    position: absolute;
    left: 128px; top: 95px;
    width: 186px; height: 225px;
    background: linear-gradient(180deg, #2a2a2a, #000000);
    border-radius: 40px 40px 16px 16px;
  }
  .brand-name-front {
    position: absolute;
    left: 0; top: 326px;
    width: 100%;
    text-align: center;
    margin: 0;
    font-size: 36px;
    font-weight: 400;
    line-height: 1.1;
    letter-spacing: 1px;
    color: var(--ink);
  }

  /* Back card */
  .portrait-back {
    position: absolute;
    left: 20px; top: 13px;
    width: 350px; height: 447px;
    background: linear-gradient(180deg, #ececec, var(--ghost));
    border-radius: 80px 80px 24px 24px;
  }
  .brand-name-back {
    position: absolute;
    right: 100px; top: 294px;
    margin: 0;
    font-size: 68px;
    font-weight: 400;
    line-height: 1;
    letter-spacing: 1px;
    color: var(--ink);
  }
  .website-back {
    position: absolute;
    right: 100px; top: 402px;
    margin: 0;
    font-size: 17px;
    letter-spacing: 1.6px;
    color: var(--muted);
  }
</style>
</head>
<body>
<main class="canvas">

  <section class="card card--front" aria-label="Card front">
    <div class="contact-panel">
      <h1 class="person-name">Marc Ravoulet</h1>
      <p class="person-role">Magician</p>
      <address class="address">
        MAGICIAN VERLINDO<br>
        17 rue des Tilleuls -<br>
        48120 VALMOREY
      </address>
      <ul class="contact-list">
        <li>
          <svg class="contact-icon" viewBox="0 0 24 24" aria-hidden="true"><path d="M6.6 10.8a15.1 15.1 0 0 0 6.6 6.6l2.2-2.2c.3-.3.7-.4 1-.2 1.1.4 2.3.6 3.6.6.6 0 1 .4 1 1V20c0 .6-.4 1-1 1A17 17 0 0 1 3 4c0-.6.4-1 1-1h3.5c.6 0 1 .4 1 1 0 1.3.2 2.5.6 3.6.1.3 0 .7-.2 1z"/></svg>
          0547 946 157
        </li>
        <li>
          <svg class="contact-icon" viewBox="0 0 24 24" aria-hidden="true"><path d="M6.6 10.8a15.1 15.1 0 0 0 6.6 6.6l2.2-2.2c.3-.3.7-.4 1-.2 1.1.4 2.3.6 3.6.6.6 0 1 .4 1 1V20c0 .6-.4 1-1 1A17 17 0 0 1 3 4c0-.6.4-1 1-1h3.5c.6 0 1 .4 1 1 0 1.3.2 2.5.6 3.6.1.3 0 .7-.2 1z"/></svg>
          0674 219 503
        </li>
        <li class="small">
          <svg class="contact-icon" viewBox="0 0 24 24" aria-hidden="true"><path d="M2 6h20v1.2l-10 6.6L2 7.2z M2 9.4l10 6.6 10-6.6V18H2z"/></svg>
          contact@verlindoillusions.example
        </li>
        <li class="small">
          <svg class="contact-icon" viewBox="0 0 24 24" aria-hidden="true"><circle cx="12" cy="12" r="10"/></svg>
          www.verlindoillusions.example
        </li>
      </ul>
    </div>
    <div class="brand-panel">
      <div class="portrait-front" role="img" aria-label="Black illustration of the magician holding a playing card"></div>
      <p class="brand-name-front">VERLINDO</p>
    </div>
  </section>

  <section class="card card--back" aria-label="Card back">
    <div class="portrait-back" role="img" aria-label="Faint grey illustration of the magician holding a playing card"></div>
    <p class="brand-name-back">VERLINDO</p>
    <p class="website-back">www.verlindoillusions.example</p>
  </section>

</main>
</body>
</html>
```